R. Velmont needs an original business card for property investment professionals

The business card would be to present me as an investor in the real estate business. The market are developers of real estate projects, or other people who would like to sell and also to give us a name as a company. For style, colour and imagery I would like something artistic from Velmont (the artist) with a different touch.

Address, email, cel phone,
Updates

Hi¡ Update¡ I;d like it to stop providing Keen Harbor as a Design and focus in R.Velmont.

Target Market(s)

Real Estate Developer/Investor

Industry/Entity Type

Real Estate

Colors
33a6d7
886aae
e3daeb
cadf82
f78f20

```html
<!DOCTYPE html>
<html lang="en">
<head>
<meta charset="utf-8">
<title>R.Velmont — Business Card</title>
<link href="https://fonts.googleapis.com/css2?family=Arimo:wght@400;700&display=swap" rel="stylesheet">
<style>
  :root {
    --stage: #e9e6e1;
    --card-paper: #e7e0d8;
    --ink-brown: #5a3f1e;
    --ink-dark: #1f1b17;
    --ink-teal: #2f4f5a;
    --art-light: #efe4d2;
    --art-mid: #c9a57a;
    --art-deep: #8a6438;
    --art-grey: #bdb8b2;
    --panel-cream: #f3ead7;
  }
  * { box-sizing: border-box; margin: 0; padding: 0; }
  html, body { width: 1200px; height: 873px; overflow: hidden; }
  body {
    background: var(--stage);
    font-family: "Arimo", Arial, sans-serif;
    position: relative;
  }
  .card {
    position: absolute;
    top: 288px;
    width: 520px;
    height: 297px;
    border-radius: 4px;
    overflow: hidden;
    box-shadow: 0 6px 18px rgba(0,0,0,0.18);
  }
  .card--front { left: 50px; background: var(--card-paper); }
  .card--back { left: 630px; }

  .front-art {
    position: absolute;
    left: 0; top: 0;
    width: 210px; height: 297px;
    clip-path: polygon(0 0, 100% 0, 34% 100%, 0 100%);
    background: linear-gradient(160deg, var(--art-deep) 0%, var(--art-mid) 40%, var(--art-light) 70%, var(--art-mid) 100%);
  }
  .brand-name {
    font-weight: 700;
    color: var(--ink-brown);
    letter-spacing: 2px;
    white-space: nowrap;
  }
  .card--front .brand-name {
    position: absolute;
    left: 200px; top: 34px;
    font-size: 40px;
  }
  .holder {
    position: absolute;
    left: 300px; top: 122px;
    color: var(--ink-dark);
  }
  .holder-name { font-size: 21px; font-weight: 700; letter-spacing: 0.5px; }
  .holder-role { font-size: 14px; margin-top: 2px; }
  .contact {
    position: absolute;
    left: 200px; top: 200px;
    list-style: none;
    color: var(--ink-dark);
    font-size: 15px;
    line-height: 1.35;
    letter-spacing: 0.3px;
  }

  .back-art {
    position: absolute; inset: 0;
    background: linear-gradient(135deg, var(--art-deep) 0%, var(--art-mid) 25%, var(--art-light) 50%, var(--art-mid) 70%, var(--art-grey) 100%);
  }
  .back-panel {
    position: absolute;
    left: 88px; top: 92px;
    width: 344px; height: 118px;
    background: linear-gradient(90deg, rgba(243,234,215,0.92), rgba(225,196,140,0.85));
    padding: 16px 20px;
  }
  .card--back .brand-name { font-size: 46px; line-height: 1; }
  .tagline {
    margin-top: 10px;
    font-size: 17px;
    color: var(--ink-teal);
    letter-spacing: 0.5px;
  }
</style>
</head>
<body>
  <section class="card card--front" aria-label="Business card front">
    <div class="front-art" role="img" aria-label="Cubist-style abstract illustration in warm browns and creams"></div>
    <h1 class="brand-name">R.VELMONT</h1>
    <div class="holder">
      <p class="holder-name">John Doe</p>
      <p class="holder-role">broker</p>
    </div>
    <ul class="contact">
      <li>adress:123 xxxxxxxxxx</li>
      <li>phone:123 456 890</li>
      <li>e-mail: info@r-velmont.com</li>
    </ul>
  </section>

  <section class="card card--back" aria-label="Business card back">
    <div class="back-art" role="img" aria-label="Cubist-style abstract cityscape illustration in sepia, cream and grey"></div>
    <div class="back-panel">
      <p class="brand-name">R.VELMONT</p>
      <p class="tagline">real estate developer/investor</p>
    </div>
  </section>
</body>
</html>
```